Business card design needed

I would like a one sided black business card with the information provided above. Refer to my website www.brightvolleyracquets.com.au for an example of colors I have used for my site, would like to keep this consistent for my business cards also, I will upload my logo below.

I am a new small business that provides tennis customers with racquet re stringing, tennis strings and accessories.

Industry/Entity Type

Small Business

Contact Information for Business Card

Bright Volley Tennis

Owen Whitby
Managing Director

brightvolleyracquets@mailbox.example
www.brightvolleyracquets.com.au
0491 726 305

Racquet Restringing/Tennis Strings/Accessories

Requirements
Must have
• Must have my logo and card must be black

```html
<!DOCTYPE html>
<html lang="en">
<head>
<meta charset="utf-8">
<title>Bright Volley Tennis – Business Card</title>
<link href="https://fonts.googleapis.com/css2?family=Arimo:wght@400;700&display=swap" rel="stylesheet">
<style>
  :root {
    --stage: #e7e4df;
    --card-black: #000000;
    --brand-blue: #234a80;
    --brand-lime: #b9d630;
    --text-white: #ffffff;
  }
  * { margin: 0; padding: 0; box-sizing: border-box; }
  html, body {
    width: 1200px;
    height: 475px;
    overflow: hidden;
    background: var(--stage);
    font-family: "Arimo", Arial, sans-serif;
  }
  .card {
    position: absolute;
    top: 81px;
    width: 547px;
    height: 313px;
    border-radius: 26px;
    background: var(--card-black);
    overflow: hidden;
  }
  .card--front { left: 31px; }
  .card--back { left: 607px; }

  .card__waves {
    position: absolute;
    inset: 0;
    width: 100%;
    height: 100%;
  }
  .wave--blue { fill: var(--brand-blue); }
  .wave--lime { fill: var(--brand-lime); }

  .brand {
    position: absolute;
    display: flex;
    align-items: center;
    gap: 10px;
    color: var(--brand-lime);
    font-weight: 700;
    text-transform: uppercase;
    white-space: nowrap;
  }
  .brand__dot {
    width: 26px;
    height: 26px;
    border-radius: 50%;
    background: var(--brand-lime);
    flex: none;
  }
  .card--front .brand {
    left: 40px;
    top: 92px;
    font-size: 27px;
  }
  .card--back .brand {
    left: 0;
    right: 0;
    top: 98px;
    justify-content: center;
    font-size: 30px;
  }

  .contact {
    position: absolute;
    right: 24px;
    top: 172px;
    text-align: right;
    color: var(--text-white);
  }
  .contact__name {
    color: var(--brand-lime);
    font-size: 17px;
    font-weight: 400;
    text-transform: uppercase;
    line-height: 20px;
  }
  .contact__role {
    color: var(--brand-lime);
    font-size: 13px;
    line-height: 18px;
    margin-bottom: 18px;
  }
  .contact__line {
    font-size: 14px;
    line-height: 18.5px;
  }

  .card__web {
    position: absolute;
    left: 0;
    right: 0;
    top: 247px;
    text-align: center;
    color: var(--text-white);
    font-size: 13px;
    letter-spacing: 1.6px;
  }
</style>
</head>
<body>

<section class="card card--front" aria-label="Business card front">
  <svg class="card__waves" viewBox="0 0 547 313" preserveAspectRatio="none" aria-hidden="true">
    <path class="wave--blue" d="M525,0 L547,0 L547,313 L0,313 L0,290 C140,300 300,250 390,180 C450,130 490,60 525,0 Z"/>
    <path class="wave--lime" d="M0,225 C70,275 240,260 400,175 C260,270 90,300 0,262 Z"/>
  </svg>

  <div class="brand">
    <span class="brand__name">Bright Volley Tennis</span>
    <span class="brand__dot"></span>
  </div>

  <div class="contact">
    <p class="contact__name">Owen Whitby</p>
    <p class="contact__role">Managing Director</p>
    <p class="contact__line">P : 0491 726 305</p>
    <p class="contact__line">E : brightvolleyracquets@mailbox.example</p>
    <p class="contact__line">W: www.brightvolleyracquets.com.au</p>
  </div>
</section>

<section class="card card--back" aria-label="Business card back">
  <div class="brand">
    <span class="brand__name">Bright Volley Tennis</span>
    <span class="brand__dot"></span>
  </div>
  <p class="card__web">www.brightvolleyracquets.com.au</p>
</section>

</body>
</html>
```